Birchline Septic Solutions

Would like to see some single sided ones but would also like to see some double sided with one sided only being the logo. Owners name is Colin Vandro. Phone number is 555-214-0387
Services are pumping, inspections, installs, and repairs

Contact Information for Business Card

555-241-0387 Colin Vandro Millbrook, OH

```html
<!DOCTYPE html>
<html lang="en">
<head>
<meta charset="utf-8">
<title>Birchline Septic Solutions – Business Cards</title>
<link href="https://fonts.googleapis.com/css2?family=Archivo:wght@400;800&display=swap" rel="stylesheet">
<style>
  :root {
    --stage: #3a3a3a;
    --card: #1b1b1c;
    --teal: #2fc4c0;
    --white: #f2f2f2;
    --muted: #d8d8d8;
    --emboss: #343436;
  }
  * { margin: 0; padding: 0; box-sizing: border-box; }
  html, body { width: 1200px; height: 801px; overflow: hidden; }
  body {
    background: var(--stage);
    font-family: "Archivo", Arial, sans-serif;
    position: relative;
  }
  .card {
    position: absolute;
    top: 252px;
    width: 520px;
    height: 297px;
    background: var(--card);
    border-bottom: 3px solid var(--teal);
    border-left: 2px solid var(--teal);
    box-shadow: 0 14px 30px rgba(0,0,0,.35);
  }
  .card--front { left: 60px; }
  .card--back { left: 620px; }

  .brand { position: absolute; color: var(--white); font-weight: 800; text-transform: uppercase; line-height: 1; }
  .brand__mark { display: inline-block; width: 10px; height: 10px; background: var(--teal); margin-right: 8px; vertical-align: middle; }
  .brand .line { display: block; }

  .card--front .brand { left: 34px; top: 72px; font-size: 21px; letter-spacing: .04em; }
  .card--front .brand .line--sub { font-size: 11px; letter-spacing: .34em; margin-top: 9px; }

  .holder { position: absolute; right: 30px; top: 34px; text-align: right; }
  .holder__name { color: var(--teal); font-weight: 800; font-size: 19px; text-transform: uppercase; letter-spacing: -.01em; }
  .holder__title { color: var(--white); font-size: 12px; margin-top: 4px; }

  .divider { position: absolute; left: 210px; right: 0; top: 150px; height: 1px; background: var(--teal); }

  .contacts { position: absolute; left: 34px; top: 180px; list-style: none; }
  .contacts li { display: flex; align-items: center; color: var(--muted); font-size: 13px; line-height: 20px; }
  .contacts svg { width: 11px; height: 11px; margin-right: 8px; fill: var(--teal); flex: none; }

  .card--back .brand {
    left: 0; right: 0; top: 112px; text-align: center;
    color: var(--emboss);
  }
  .card--back .brand .line--main { font-size: 44px; letter-spacing: .06em; }
  .card--back .brand .line--sub { font-size: 16px; letter-spacing: .38em; margin-top: 10px; }
</style>
</head>
<body>
  <section class="card card--front" aria-label="Business card front">
    <div class="brand">
      <span class="line"><i class="brand__mark"></i>Birchline</span>
      <span class="line line--sub">Septic Solutions</span>
    </div>
    <div class="holder">
      <p class="holder__name">Colin Vandro</p>
      <p class="holder__title">Founder / CEO</p>
    </div>
    <div class="divider"></div>
    <ul class="contacts">
      <li><svg viewBox="0 0 24 24"><path d="M6.6 10.8a15 15 0 0 0 6.6 6.6l2.2-2.2a1 1 0 0 1 1-.25 11.4 11.4 0 0 0 3.6.57 1 1 0 0 1 1 1V20a1 1 0 0 1-1 1A17 17 0 0 1 3 4a1 1 0 0 1 1-1h3.5a1 1 0 0 1 1 1c0 1.25.2 2.45.57 3.57a1 1 0 0 1-.25 1z"/></svg>555-241-0387</li>
      <li><svg viewBox="0 0 24 24"><path d="M2 5h20v14H2zm2 2v.5l8 5 8-5V7l-8 5z"/></svg>info@birchlineseptic.com</li>
      <li><svg viewBox="0 0 24 24"><circle cx="12" cy="12" r="10"/></svg>www.birchlineseptic.com</li>
      <li><svg viewBox="0 0 24 24"><path d="M12 2a7 7 0 0 0-7 7c0 5 7 13 7 13s7-8 7-13a7 7 0 0 0-7-7zm0 9.5A2.5 2.5 0 1 1 12 6.5a2.5 2.5 0 0 1 0 5z"/></svg>Millbrook, OH</li>
    </ul>
  </section>

  <section class="card card--back" aria-label="Business card back">
    <div class="brand">
      <span class="line line--main">Birchline</span>
      <span class="line line--sub">Septic Solutions</span>
    </div>
  </section>
</body>
</html>
```